Elegant, professional powerpoint design for Vorlane Engineering and Mining SARLU

I’ve created a new Sub contracting company for mining industry in the Democratic Republic of Congo. With Plumviser, I’ve created a logo. I would want a professional and beautiful powerpoint design which I will use to sell my services to mining companies in DRC. The powerpoint must have pictures of mining engines such as excavators, drones, trucks, etc

```html
<!DOCTYPE html>
<html lang="en">
<head>
<meta charset="utf-8">
<title>Vorlane Engineering and Mining – Presentation</title>
<link href="https://fonts.googleapis.com/css2?family=Krona+One&family=Montserrat:wght@500;600;700&family=Poppins:wght@400;500;600&display=swap" rel="stylesheet">
<style>
:root{
  --page:#e4e6e9;
  --navy:#1b2687;
  --royal:#26309a;
  --gold:#f39c12;
  --bronze:#c9821b;
  --ink:#1c1c1c;
  --body:#5a5a5a;
  --line:#d9d9d9;
  --white:#ffffff;
  --green:#3ab65b;
  --pink:#e6186e;
  --violet:#6a2be0;
  --teal:#43cdb5;
}
*{margin:0;padding:0;box-sizing:border-box}
html,body{width:1200px;height:4147px;overflow:hidden;background:var(--page)}
body{position:relative;font-family:"Poppins",sans-serif;color:var(--body)}
.slide{position:absolute;left:52px;width:1097px;height:617px;background:var(--white);overflow:hidden}
.s1{top:52px;background:linear-gradient(135deg,#2a33a0,#1d2790 60%,#1a2283)}
.s2{top:736px}.s3{top:1421px}.s4{top:2104px}.s5{top:2789px}.s6{top:3473px}
.abs{position:absolute}

/* brand */
.brand{display:flex;flex-direction:column;align-items:center;gap:6px}
.brand-mark{width:46px;height:46px;border-radius:50%;background:var(--bronze)}
.brand-name{font-family:"Krona One",sans-serif;color:var(--white);letter-spacing:1px}
.brand-sub{font-family:"Poppins",sans-serif;color:var(--gold);font-weight:500;letter-spacing:1.2px}
.brand-box{left:0;top:0;width:171px;height:129px;background:var(--navy);padding-top:24px}
.brand-box .brand-mark{width:34px;height:34px}
.brand-box .brand-name{font-size:14px}
.brand-box .brand-sub{font-size:6px;margin-top:-4px}

/* cover */
.cover-brand{left:77px;top:80px;align-items:flex-start}
.cover-brand .brand-mark{width:60px;height:60px;margin-left:60px}
.cover-brand .brand-name{font-size:27px}
.cover-brand .brand-sub{font-size:10.5px;margin-top:-5px}
.cover-title{left:77px;top:300px;font-family:"Krona One",sans-serif;font-size:48px;color:var(--white);letter-spacing:1px}
.cover-text{left:79px;top:368px;width:400px;font-size:11.5px;line-height:22.6px;color:#e6e8f5;text-align:justify}

/* shared */
.slide-title{right:52px;top:38px;font-family:"Krona One",sans-serif;font-size:27px;color:var(--ink);letter-spacing:2px}
.title-arrow{right:0;top:42px}
.footer{left:0;bottom:0;width:100%;height:57px;background:var(--navy)}
.copyright{left:39px;top:20px;font-size:10.5px;color:var(--white)}
.socials{left:836px;top:17px;display:flex;gap:5px}
.socials span{width:21px;height:21px;border-radius:50%;background:var(--white);display:block}
.notch{left:950px;top:484px}
.page-no{right:22px;bottom:12px;font-size:18px;color:var(--white);font-family:"Poppins",sans-serif}

/* about */
.about-text{left:555px;top:136px;width:494px;font-size:11px;line-height:22.8px;color:var(--body);text-align:justify}
.about-text p+p{margin-top:22px}

/* services */
.service{width:483px;height:162px;border:1px solid var(--line);padding:20px 28px 0 68px}
.service .num{position:absolute;left:27px;top:18px;font-size:38px;color:var(--gold);font-weight:400}
.service h3{font-family:"Montserrat",sans-serif;font-weight:700;font-size:22px;color:var(--ink)}
.service p{margin-top:10px;font-size:11px;line-height:20px;color:var(--body)}

/* timeline */
.pill{top:352px;width:172px;height:42px;border-radius:21px;color:var(--white);font-size:14px;font-weight:500;display:flex;align-items:center;justify-content:center}
.step-text{top:410px;width:190px;font-size:14px;line-height:19.5px;color:var(--body);white-space:nowrap}

/* team */
.member{top:200px;width:200px;text-align:center}
.member .name{margin-top:16px;font-family:"Montserrat",sans-serif;font-weight:600;font-size:17px;color:var(--ink)}
.member .company{margin-top:2px;font-weight:600;font-size:11px;color:var(--bronze)}

/* thank you */
.contact{right:175px;text-align:right}
.contact .label{font-size:18px;color:var(--ink)}
.contact .value{margin-top:4px;font-size:11.5px;color:var(--ink)}
.contact .value.big{font-size:20px;font-weight:500;color:#333}
.contact-icon{left:948px}
</style>
</head>
<body>

<!-- Cover -->
<section class="slide s1">
  <svg class="abs" style="left:0;top:0" width="1097" height="617" viewBox="0 0 1097 617">
    <defs>
      <linearGradient id="coverSky" x1="1" y1="0" x2="0" y2="1"><stop offset="0" stop-color="#cfd0d2"/><stop offset=".55" stop-color="#8e9095"/><stop offset="1" stop-color="#3f4147"/></linearGradient>
      <radialGradient id="coverTruck" cx=".68" cy=".55" r=".38"><stop offset="0" stop-color="#e7a21c" stop-opacity=".9"/><stop offset=".6" stop-color="#c58a22" stop-opacity=".45"/><stop offset="1" stop-color="#8e9095" stop-opacity="0"/></radialGradient>
    </defs>
    <polygon points="1045,10 1097,10 1097,617 430,617 470,583" fill="var(--gold)"/>
    <g role="img" aria-label="Photo of a loaded yellow mining haul truck on a quarry road">
      <polygon points="1076,20 1076,583 440,583" fill="url(#coverSky)"/>
      <polygon points="1076,20 1076,583 440,583" fill="url(#coverTruck)"/>
    </g>
  </svg>
  <div class="abs brand cover-brand">
    <span class="brand-mark"></span>
    <span class="brand-name">VORLANE</span>
    <span class="brand-sub">ENGINEERING AND MINING</span>
  </div>
  <h1 class="abs cover-title">VORLANE</h1>
  <p class="abs cover-text">Lorem ipsum dolor sit amet, consectetur adipiscing elit, sed do eiusmod tempor incididunt ut labore et dolore magna aliqua. Ut enim ad minim veniam, quis nostrud exercitation ullamco laboris nisi ut aliquip ex ea commodo consequat.</p>
</section>

<!-- About -->
<section class="slide s2">
  <div class="abs brand brand-box"><span class="brand-mark"></span><span class="brand-name">VORLANE</span><span class="brand-sub">ENGINEERING AND MINING</span></div>
  <h2 class="abs slide-title">ABOUT VORLANE</h2>
  <svg class="abs title-arrow" width="26" height="24"><polygon points="0,12 26,0 26,24" fill="var(--gold)"/></svg>
  <svg class="abs" style="left:101px;top:88px" width="411" height="448" viewBox="0 0 411 448">
    <defs><linearGradient id="dustGrad" x1="0" y1="0" x2=".3" y2="1"><stop offset="0" stop-color="#3f4658"/><stop offset=".3" stop-color="#767b86"/><stop offset=".55" stop-color="#c3c5c8"/><stop offset=".8" stop-color="#7a7670"/><stop offset="1" stop-color="#4d4b48"/></linearGradient></defs>
    <polygon points="205,0 411,112 411,336 205,448 0,336 0,112" fill="url(#dustGrad)" role="img" aria-label="Photo of haul trucks raising dust on an open-pit mine road"/>
  </svg>
  <div class="abs about-text">
    <p>Lorem ipsum dolor sit amet, consectetur adipiscing elit, sed do eiusmod tempor incididunt ut labore et dolore magna aliqua. Ut enim ad minim veniam, quis nostrud exercitation ullamco laboris nisi ut aliquip ex ea commodo consequat.</p>
    <p>Sed ut perspiciatis unde omnis iste natus error sit voluptatem accusantium doloremque laudantium, totam rem aperiam, eaque ipsa quae ab illo inventore veritatis et quasi architecto beatae vitae dicta sunt explicabo. Nemo enim ipsam voluptatem quia voluptas sit aspernatur aut odit aut fugit, sed quia consequuntur magni dolores eos qui ratione voluptatem sequi nesciunt. Neque porro quisquam est, qui dolorem ipsum quia dolor sit amet, consectetur, adipisci velit, sed quia non numquam eius modi tempora incidunt ut labore et dolore magnam aliquam quaerat voluptatem. Ut enim ad minima veniam, quis nostrum exercitationem ullam corporis suscipit laboriosam, nisi ut aliquid ex ea commodi consequatur? Quis autem vel eum iure reprehenderit qui in ea voluptate velit esse quam nihil molestiae consequatur, vel illum qui dolorem eum fugiat quo voluptas nulla pariatur</p>
  </div>
  <div class="abs footer"><span class="abs copyright">© Copyrights 2023 The Company Name | All Rights Reserved</span><div class="abs socials"><span></span><span></span><span></span><span></span></div></div>
  <svg class="abs notch" width="96" height="133"><polygon points="48,0 96,27 96,106 48,133 0,106 0,27" fill="var(--white)"/><circle cx="48" cy="56" r="30" fill="var(--bronze)"/></svg>
  <span class="abs page-no">02</span>
</section>

<!-- Services -->
<section class="slide s3">
  <div class="abs brand brand-box"><span class="brand-mark"></span><span class="brand-name">VORLANE</span><span class="brand-sub">ENGINEERING AND MINING</span></div>
  <h2 class="abs slide-title">OUR SERVICES</h2>
  <svg class="abs title-arrow" width="26" height="24"><polygon points="0,12 26,0 26,24" fill="var(--gold)"/></svg>
  <div class="abs service" style="left:53px;top:149px"><span class="num">1</span><h3>Nemo enim ipsam volup</h3><p>Lorem ipsum dolor sit amet, consectetur adipiscing elit, sed do eiusmod tempor incididunt ut labore et dolore magna aliqua. Ut enim ad minim veniam, quis nostrud exercitation ullamco laboris nisi ut aliquip ex ea commodo consequat.</p></div>
  <div class="abs service" style="left:560px;top:149px"><span class="num">2</span><h3>Nemo enim ipsam volup</h3><p>Lorem ipsum dolor sit amet, consectetur adipiscing elit, sed do eiusmod tempor incididunt ut labore et dolore magna aliqua. Ut enim ad minim veniam, quis nostrud exercitation ullamco laboris nisi ut aliquip ex ea commodo consequat.</p></div>
  <div class="abs service" style="left:53px;top:325px"><span class="num">3</span><h3>Nemo enim ipsam volup</h3><p>Lorem ipsum dolor sit amet, consectetur adipiscing elit, sed do eiusmod tempor incididunt ut labore et dolore magna aliqua. Ut enim ad minim veniam, quis nostrud exercitation ullamco laboris nisi ut aliquip ex ea commodo consequat.</p></div>
  <div class="abs service" style="left:560px;top:325px"><span class="num">4</span><h3>Nemo enim ipsam volup</h3><p>Lorem ipsum dolor sit amet, consectetur adipiscing elit, sed do eiusmod tempor incididunt ut labore et dolore magna aliqua. Ut enim ad minim veniam, quis nostrud exercitation ullamco laboris nisi ut aliquip ex ea commodo consequat.</p></div>
  <div class="abs footer"><span class="abs copyright">© Copyrights 2023 The Company Name | All Rights Reserved</span><div class="abs socials"><span></span><span></span><span></span><span></span></div></div>
  <svg class="abs notch" width="96" height="133"><polygon points="48,0 96,27 96,106 48,133 0,106 0,27" fill="var(--white)"/><circle cx="48" cy="56" r="30" fill="var(--bronze)"/></svg>
  <span class="abs page-no">03</span>
</section>

<!-- Timeline -->
<section class="slide s4">
  <div class="abs brand brand-box"><span class="brand-mark"></span><span class="brand-name">VORLANE</span><span class="brand-sub">ENGINEERING AND MINING</span></div>
  <h2 class="abs slide-title">TIMELINE</h2>
  <svg class="abs title-arrow" width="26" height="24"><polygon points="0,12 26,0 26,24" fill="var(--gold)"/></svg>
  <svg class="abs" style="left:0;top:120px" width="1097" height="220" viewBox="0 0 1097 220">
    <defs>
      <radialGradient id="iconGreen"><stop offset="0" stop-color="#3ab65b" stop-opacity=".22"/><stop offset="1" stop-color="#3ab65b" stop-opacity="0"/></radialGradient>
      <radialGradient id="iconPink"><stop offset="0" stop-color="#e6186e" stop-opacity=".2"/><stop offset="1" stop-color="#e6186e" stop-opacity="0"/></radialGradient>
      <radialGradient id="iconViolet"><stop offset="0" stop-color="#6a2be0" stop-opacity=".18"/><stop offset="1" stop-color="#6a2be0" stop-opacity="0"/></radialGradient>
      <radialGradient id="iconTeal"><stop offset="0" stop-color="#43cdb5" stop-opacity=".22"/><stop offset="1" stop-color="#43cdb5" stop-opacity="0"/></radialGradient>
    </defs>
    <path d="M148,102 V178 a22,22 0 0 0 22,22 H324 a22,22 0 0 0 22,-22 V42 a22,22 0 0 1 22,-22 H525 a22,22 0 0 1 22,22 V178 a22,22 0 0 0 22,22 H727 a22,22 0 0 0 22,-22 V42 a22,22 0 0 1 22,-22 H927 a22,22 0 0 1 22,22 V90" fill="none" stroke="#8a6fc4" stroke-width="2"/>
    <polygon points="942,88 956,88 949,102" fill="var(--violet)"/>
    <circle cx="148" cy="102" r="8" fill="var(--green)"/>
    <circle cx="346" cy="102" r="8" fill="var(--pink)"/>
    <circle cx="547" cy="102" r="8" fill="var(--violet)"/>
    <circle cx="749" cy="102" r="8" fill="var(--teal)"/>
    <ellipse cx="245" cy="110" rx="70" ry="62" fill="url(#iconGreen)" role="img" aria-label="Line illustration of a bank, documents and a person"/>
    <ellipse cx="447" cy="100" rx="72" ry="62" fill="url(#iconPink)" role="img" aria-label="Line illustration of money, scales and a magnifier"/>
    <ellipse cx="648" cy="110" rx="66" ry="62" fill="url(#iconViolet)" role="img" aria-label="Line illustration of a hand with coins, a checklist and a person"/>
    <ellipse cx="850" cy="100" rx="74" ry="62" fill="url(#iconTeal)" role="img" aria-label="Line illustration of a calculator, pie chart and growth arrow"/>
  </svg>
  <div class="abs pill" style="left:159px;background:var(--green)">Nemo enim ipsam</div>
  <div class="abs pill" style="left:359px;background:var(--pink)">Nemo enim ipsam</div>
  <div class="abs pill" style="left:559px;background:var(--violet)">Nemo enim ipsam</div>
  <div class="abs pill" style="left:759px;background:var(--teal)">Nemo enim ipsam</div>
  <p class="abs step-text" style="left:164px">Lorem ipsum dolor sit dim<br>amet, mea regione diamet<br>principes at. Cum no movi<br>lorem ipsum dolor sit dim</p>
  <p class="abs step-text" style="left:362px">Lorem ipsum dolor sit dim<br>amet, mea regione diamet<br>principes at. Cum no movi<br>lorem ipsum dolor sit dim</p>
  <p class="abs step-text" style="left:563px">Lorem ipsum dolor sit dim<br>amet, mea regione diamet<br>principes at. Cum no movi<br>lorem ipsum dolor sit dim</p>
  <p class="abs step-text" style="left:763px">Lorem ipsum dolor sit dim<br>amet, mea regione diamet<br>principes at. Cum no movi<br>lorem ipsum dolor sit dim</p>
  <div class="abs footer"><span class="abs copyright">© Copyrights 2023 The Company Name | All Rights Reserved</span><div class="abs socials"><span></span><span></span><span></span><span></span></div></div>
  <svg class="abs notch" width="96" height="133"><polygon points="48,0 96,27 96,106 48,133 0,106 0,27" fill="var(--white)"/><circle cx="48" cy="56" r="30" fill="var(--bronze)"/></svg>
  <span class="abs page-no">04</span>
</section>

<!-- Team -->
<section class="slide s5">
  <div class="abs brand brand-box"><span class="brand-mark"></span><span class="brand-name">VORLANE</span><span class="brand-sub">ENGINEERING AND MINING</span></div>
  <h2 class="abs slide-title">OUR TEAM</h2>
  <svg class="abs title-arrow" width="26" height="24"><polygon points="0,12 26,0 26,24" fill="var(--gold)"/></svg>
  <svg class="abs" width="0" height="0"><defs>
    <linearGradient id="portraitA" x1="0" y1="0" x2="0" y2="1"><stop offset="0" stop-color="#b5b3b0"/><stop offset="1" stop-color="#8f7f6c"/></linearGradient>
    <linearGradient id="portraitB" x1="0" y1="0" x2="0" y2="1"><stop offset="0" stop-color="#d6d7da"/><stop offset="1" stop-color="#5b6e8c"/></linearGradient>
    <linearGradient id="portraitC" x1="0" y1="0" x2="0" y2="1"><stop offset="0" stop-color="#3f74ad"/><stop offset="1" stop-color="#6d9fd0"/></linearGradient>
    <linearGradient id="portraitD" x1="0" y1="0" x2="0" y2="1"><stop offset="0" stop-color="#e6e9ed"/><stop offset="1" stop-color="#8fb0d6"/></linearGradient>
  </defs></svg>
  <div class="abs member" style="left:96px"><svg width="152" height="170" viewBox="0 0 152 170"><polygon points="76,0 152,42 152,128 76,170 0,128 0,42" fill="url(#portraitA)" role="img" aria-label="Portrait photo of a team member"/></svg><div class="name">John Doe</div><div class="company">Company Name</div></div>
  <div class="abs member" style="left:336px"><svg width="152" height="170" viewBox="0 0 152 170"><polygon points="76,0 152,42 152,128 76,170 0,128 0,42" fill="url(#portraitB)" role="img" aria-label="Portrait photo of a team member"/></svg><div class="name">John Doe</div><div class="company">Company Name</div></div>
  <div class="abs member" style="left:579px"><svg width="152" height="170" viewBox="0 0 152 170"><polygon points="76,0 152,42 152,128 76,170 0,128 0,42" fill="url(#portraitC)" role="img" aria-label="Portrait photo of a team member"/></svg><div class="name">John Doe</div><div class="company">Company Name</div></div>
  <div class="abs member" style="left:821px"><svg width="152" height="170" viewBox="0 0 152 170"><polygon points="76,0 152,42 152,128 76,170 0,128 0,42" fill="url(#portraitD)" role="img" aria-label="Portrait photo of a team member"/></svg><div class="name">John Doe</div><div class="company">Company Name</div></div>
  <div class="abs footer"><span class="abs copyright">© Copyrights 2023 The Company Name | All Rights Reserved</span><div class="abs socials"><span></span><span></span><span></span><span></span></div></div>
  <svg class="abs notch" width="96" height="133"><polygon points="48,0 96,27 96,106 48,133 0,106 0,27" fill="var(--white)"/><circle cx="48" cy="56" r="30" fill="var(--bronze)"/></svg>
  <span class="abs page-no">05</span>
</section>

<!-- Thank you -->
<section class="slide s6">
  <div class="abs" style="left:0;top:0;width:1097px;height:617px;background:linear-gradient(90deg,rgba(255,255,255,0) 0%,rgba(255,255,255,0) 45%,#f3ede4 68%,#ffffff 82%),linear-gradient(180deg,#8a7a66 0%,#c79a4e 35%,#b57f2a 70%,#9c7a55 100%)" role="img" aria-label="Photo of a convoy of yellow mining haul trucks on a dusty road"></div>
  <div class="abs brand brand-box"><span class="brand-mark"></span><span class="brand-name">VORLANE</span><span class="brand-sub">ENGINEERING AND MINING</span></div>
  <h2 class="abs slide-title">THANK YOU</h2>
  <svg class="abs title-arrow" width="26" height="24"><polygon points="0,12 26,0 26,24" fill="var(--gold)"/></svg>
  <div class="abs" style="left:1038px;top:122px;width:3px;height:412px;background:var(--gold)"></div>
  <div class="abs contact" style="top:141px"><div class="label">Address :</div><div class="value">123, Lorem ipsum dolor sit amet, cons</div></div>
  <div class="abs contact" style="top:263px"><div class="label">Email Address :</div><div class="value">info@companyname.com</div></div>
  <div class="abs contact" style="top:386px"><div class="label">Phone :</div><div class="value big">+1 888 888 8888</div></div>
  <svg class="abs contact-icon" style="top:131px" width="60" height="62" viewBox="0 0 60 62"><polygon points="30,0 60,16 60,46 30,62 0,46 0,16" fill="var(--gold)"/><path d="M30,19 a8,8 0 0 1 8,8 c0,6 -8,15 -8,15 c0,0 -8,-9 -8,-15 a8,8 0 0 1 8,-8z" fill="var(--ink)"/><circle cx="30" cy="27" r="3" fill="var(--gold)"/></svg>
  <svg class="abs contact-icon" style="top:253px" width="60" height="62" viewBox="0 0 60 62"><polygon points="30,0 60,16 60,46 30,62 0,46 0,16" fill="var(--gold)"/><rect x="19" y="23" width="22" height="16" rx="2" fill="var(--ink)"/><path d="M19,24 L30,32 L41,24" fill="none" stroke="var(--gold)" stroke-width="2"/></svg>
  <svg class="abs contact-icon" style="top:376px" width="60" height="62" viewBox="0 0 60 62"><polygon points="30,0 60,16 60,46 30,62 0,46 0,16" fill="var(--gold)"/><path d="M22,22 l5,-2 3,6 -3,3 c1.5,3 3.5,5 6.5,6.5 l3,-3 6,3 -2,5 c-10,0 -18.5,-8.5 -18.5,-18.5z" fill="var(--ink)"/></svg>
  <div class="abs footer"><span class="abs copyright">© Copyrights 2023 The Company Name | All Rights Reserved</span><div class="abs socials"><span></span><span></span><span></span><span></span></div></div>
  <svg class="abs notch" width="96" height="133"><polygon points="48,0 96,27 96,106 48,133 0,106 0,27" fill="var(--white)"/><circle cx="48" cy="56" r="30" fill="var(--bronze)"/></svg>
  <span class="abs page-no">06</span>
</section>

</body>
</html>
```